new service company in the field of construction seeks to make the Creation of a PPT

We need a PPT format with a cover page a frame for presentation. our company is based in Paris which was named VORENTIX. we just did our logo attached. Our company offers services to manage and control documents that pass on projects in construction (building, infrastructure, energy, oil and gas etc. ..). We use internet systems to help us, design must show insurance, quality, and safety. Customers should build any type of works and can not build without the approved documents. These documents go through multiple validations, and vorentix staff seconded on projects, coordinate these processes and documents, quality documents, to ensure that project deadlines are met and project management sees his project developed within the period, through regular reporting. the services offered by our company help ensure the project of building on time, to ensure the project manager visibility on what e will not, and can act accordingly.

Target Market(s)

general contractor of engineering construction or big business masters lumber wholesale real estate investor, project ownership in the construction sector

Industry/Entity Type

Construction

Contact Information for Business Card

carte rectangulaire petite taille (4X6cm env)
horizontale ou verticale
prendre en compte les éléments suivants :
logo
nom de société
adresse postale (4 lignes)
teléphone:
mail
role (ex : directeur)
in the back : La qualité documentaire de vos projets

Font styles to use
Sans Serif

Colors
34a7d7
85cae6
cee9f5
0592cd

Requirements
Must have
• The project should have 2 sliders: slider 1. Cover Page 2. slider for the content of presentations THE GOAL IS TO HAVE A VISUAL IDENTITY ON PPT, MY BUSINESS CARDS AND LETTERS must stay in mind and colors of the logo that joined the design must be clean and recall the seriousness, ease. the design must take into account the page numbers Tag line: the documentary quality of your projects information such as tagline and writes must be modifiable
Nice to have
• would require the presentation of the figure shows concepts or reporting table THE GOAL IS TO HAVE A VISUAL IDENTITY ON PPT, MY BUSINESS CARDS AND LETTERS
Should not have
• not to building or building in the logo

```html
<!DOCTYPE html>
<html lang="en">
<head>
<meta charset="utf-8">
<title>VORENTIX – Presentation Template</title>
<link href="https://fonts.googleapis.com/css2?family=Raleway:wght@400;500;600;700&display=swap" rel="stylesheet">
<style>
:root{
  --blue:#0592cd;
  --blue-deep:#0578a8;
  --blue-mid:#34a7d7;
  --blue-light:#85cae6;
  --blue-pale:#cee9f5;
  --gray-dark:#5f5f5f;
  --gray:#8a8a8a;
  --gray-light:#c4c4c4;
  --row:#ececec;
  --row-alt:#dddddd;
  --text:#7d7d7d;
  --white:#ffffff;
}
*{box-sizing:border-box;margin:0;padding:0}
html,body{width:1200px;height:908px;overflow:hidden;background:var(--white)}
body{font-family:'Raleway',sans-serif;position:relative;color:var(--text)}
.slide{position:absolute;width:387px;height:218px;background:var(--white);overflow:hidden;box-shadow:0 0 0 1px #e2e2e2}
.c1{left:6px}.c2{left:406px}.c3{left:806px}
.r1{top:4px}.r2{top:228px}.r3{top:452px}.r4{top:676px}
.abs{position:absolute}
.title{position:absolute;left:17px;top:14px;font-size:17px;color:var(--blue);font-weight:400;white-space:nowrap}
.title .u{text-decoration:underline;text-underline-offset:3px;text-decoration-thickness:1px}
.brand{position:absolute;right:10px;top:16px;display:flex;align-items:center;gap:3px;font-weight:700;font-size:9px;color:var(--blue);letter-spacing:.3px}
.brand .dot{width:9px;height:9px;border-radius:50%;background:var(--blue)}
.lead{position:absolute;left:17px;right:17px;top:60px;font-size:5px;line-height:1.4;color:var(--text)}
.footer{position:absolute;left:0;right:0;bottom:0;height:8px;background:var(--blue);color:var(--white);font-size:4px;line-height:8px;padding-left:5px}
.page{position:absolute;right:10px;bottom:0;width:16px;height:8px;background:var(--blue-pale);color:var(--blue-deep);font-size:4px;line-height:8px;text-align:center}
.small{font-size:4.6px;line-height:1.35;color:var(--text)}
.head-s{font-size:6px;color:var(--blue-mid);font-weight:500}
.photo{position:absolute}
/* Video slide */
.video-band{position:absolute;left:0;top:0;width:387px;height:108px;background:linear-gradient(90deg,var(--blue-mid),var(--blue-light) 60%,var(--blue-pale))}
.video-band h2{position:absolute;left:17px;top:20px;font-size:15px;font-weight:400;color:var(--white)}
.video-band h3{position:absolute;left:10px;top:54px;font-size:8px;font-weight:400;color:var(--white)}
.video-band p{position:absolute;left:10px;top:66px;width:145px;font-size:4.6px;line-height:1.35;color:var(--white)}
.video-still{left:157px;top:10px;width:200px;height:172px;background:linear-gradient(160deg,#d7e2ea,#9fb1c1 55%,#6d8296)}
.feature{position:absolute;left:14px;width:146px;display:flex;gap:6px}
.feature .ico{flex:0 0 10px;height:10px;border-radius:50%;background:var(--blue);margin-top:1px}
/* Four column */
.box{position:absolute;top:78px;width:68px;height:90px;color:var(--white);text-align:center}
.box.dark{background:var(--blue)}
.box.light{background:var(--blue-light)}
.box .ring{width:14px;height:14px;border-radius:50%;border:1px solid rgba(255,255,255,.8);margin:14px auto 0}
.box .lbl{font-size:4.8px;margin-top:14px}
.box .txt{font-size:4.8px;line-height:1.3;margin-top:4px;padding:0 10px}
.col{position:absolute;top:72px;width:72px;text-align:center}
.col .circ{width:42px;height:42px;border-radius:50%;margin:0 auto;border:4px solid var(--blue-light);background:var(--white);display:flex;align-items:center;justify-content:center}
.col .circ.dk{border-color:var(--blue)}
.col .circ i{display:block;width:14px;height:14px;border-radius:50%;background:var(--blue-light)}
.col .circ.dk i{background:var(--blue)}
.col h4{font-size:5.5px;font-weight:700;color:var(--blue);margin-top:6px}
.col h4.lt{color:var(--blue-light)}
.col p{margin-top:5px}
.vline{position:absolute;top:70px;width:1px;height:118px;background:#e6e6e6}
/* Timeline */
.tl{position:absolute;border-radius:50%;color:var(--white);text-align:center;font-size:9px;display:flex;flex-direction:column;justify-content:center;align-items:center}
.tl small{font-size:3.5px;line-height:1.2;width:60%}
/* Table */
.grid{position:absolute;left:4px;top:38px;width:376px;border-collapse:collapse;table-layout:fixed;font-size:3.8px}
.grid th{background:var(--blue);color:var(--white);font-weight:500;height:28px;border-right:1px solid #fff;text-align:center}
.grid th:first-child{text-align:left;padding-left:5px}
.grid th small{display:block;font-size:3.4px;margin-top:2px}
.grid td{height:8.4px;border-right:1px solid #fff;color:#777}
.grid td:first-child{padding-left:5px}
.grid tr:nth-child(odd) td{background:var(--row)}
.grid tr:nth-child(even) td{background:var(--row-alt)}
.chk{display:block;margin:0 auto;width:6px;height:6px;border-radius:50%;background:var(--gray);color:#fff;font-size:4px;line-height:6px;text-align:center;font-style:normal}
.chk.o{background:transparent;border:0.6px solid var(--gray);color:var(--gray)}
/* Bullets */
.bul{position:absolute;display:flex;gap:7px;width:150px}
.bul .ico{flex:0 0 12px;height:12px;border-radius:50%;background:var(--blue)}
.bul .ico.lt{background:var(--blue-light)}
.bul .ico.gd{background:var(--gray-dark)}
.bul .ico.gl{background:var(--gray-light)}
.bul h5{font-size:6px;font-weight:400;color:var(--blue)}
.bul h5.lt{color:var(--blue-light)}
/* Our infographic */
.strip{position:absolute;left:128px;width:184px;height:17px;color:#fff;font-size:4.3px;line-height:1.3;padding:2px 6px 0 34px}
.strip.dk{background:var(--blue)}
.strip.lt{background:var(--blue-light)}
/* Team */
.person{position:absolute;text-align:center;width:80px}
.person .face{width:34px;height:34px;border-radius:50%;margin:0 auto;border:2px solid #fff;box-shadow:0 0 0 1px #ddd;background:linear-gradient(#c9b8a8,#6e6762)}
.person b{display:block;font-size:5.5px;font-weight:500;color:#555;margin-top:2px}
.person span{display:block;font-size:3.8px;color:var(--blue)}
.person em{display:block;font-style:normal;font-size:3.6px;color:#999}
/* Contact */
.contact-bg{left:0;top:0;width:387px;height:218px;background:linear-gradient(120deg,var(--blue-mid),var(--blue-light) 55%,var(--blue-pale))}
.contact-panel{position:absolute;left:0;top:0;width:164px;height:218px;background:rgba(5,146,205,.8)}
.contact-brand{position:absolute;left:0;width:164px;top:24px;text-align:center;color:#fff;font-weight:700;font-size:12px;letter-spacing:.5px}
.contact-brand .dot{display:block;width:13px;height:13px;border-radius:50%;background:#fff;margin:0 auto 5px}
.contact-title{position:absolute;left:50px;top:76px;font-size:14px;font-weight:400;color:#fff}
.contact-title span{text-decoration:underline;text-underline-offset:3px;text-decoration-thickness:1px}
.cline{position:absolute;left:50px;display:flex;gap:8px;color:#fff;font-size:6px;line-height:1.3}
.cline svg{flex:0 0 7px;margin-top:1px}
.social{position:absolute;left:70px;top:204px;display:flex;gap:6px}
.social i{width:8px;height:8px;border-radius:50%;background:#fff}
.thanks{position:absolute;left:164px;width:223px;top:112px;text-align:center;color:#fff}
.thanks h2{font-size:18px;font-weight:700;letter-spacing:.5px}
.thanks h3{font-size:7px;font-weight:400;margin-top:1px}
.thanks p{font-size:5.5px;margin-top:6px;line-height:1.3}
</style>
</head>
<body>

<!-- Slide: video area -->
<section class="slide c1 r1">
  <div class="video-band">
    <h2><span style="text-decoration:underline;text-underline-offset:3px;text-decoration-thickness:1px">Our</span> Video Area</h2>
    <h3>Heading Here</h3>
    <p>Lorem ipsum dolor sit amet, consectetur adipiscing elit, sed do eiusmod tempor incididunt ut labore et dolore magna aliqua. Ut enimad minim veniam, quis nostrud exercitation ullamco laboris</p>
  </div>
  <div class="photo video-still" role="img" aria-label="Desktop monitor showing a video of engineers in hard hats reviewing plans"></div>
  <div class="feature" style="top:116px"><span class="ico"></span><p class="small">Lorem ipsum dolor sit amet, consectetur adipiscing elit, sed do eiusmod tempor incididunt ut labore et dolore magna aliqua. Ut enimad minim veniam, quis nostrud</p></div>
  <div class="feature" style="top:144px"><span class="ico"></span><p class="small">Lorem ipsum dolor sit amet, consectetur adipiscing elit, sed do eiusmod tempor incididunt ut labore et dolore magna aliqua. Ut enimad minim veniam, quis nostrud</p></div>
  <div class="feature" style="top:172px"><span class="ico"></span><p class="small">Lorem ipsum dolor sit amet, consectetur adipiscing elit, sed do eiusmod tempor incididunt ut labore et dolore magna aliqua. Ut enimad minim veniam, quis nostrud</p></div>
</section>

<!-- Slide: four column boxes -->
<section class="slide c2 r1">
  <h2 class="title"><span class="u">Four</span> Column Area</h2>
  <div class="brand"><span class="dot"></span>VORENTIX</div>
  <p class="lead" style="top:56px;text-align:center">Lorem ipsum dolor sit amet, consectetur adipiscing elit, sed do eiusmod tempor incididunt ut labore et dolore magna aliqua. Ut enimad minim veniam, quis nostrud exercitation ullamco laboris nisi ut aliquip ex ea commodo consequat.</p>
  <div class="box dark" style="left:28px"><div class="ring"></div><div class="lbl">YOUR TEXT HERE</div><div class="txt">Lorem ipsum dolor sit consectetur adipiscing elit.</div></div>
  <div class="box light" style="left:108px"><div class="ring"></div><div class="lbl">YOUR TEXT HERE</div><div class="txt">Lorem ipsum dolor sit consectetur adipiscing elit.</div></div>
  <div class="box dark" style="left:189px"><div class="ring"></div><div class="lbl">YOUR TEXT HERE</div><div class="txt">Lorem ipsum dolor sit consectetur adipiscing elit.</div></div>
  <div class="box light" style="left:270px"><div class="ring"></div><div class="lbl">YOUR TEXT HERE</div><div class="txt">Lorem ipsum dolor sit consectetur adipiscing elit.</div></div>
  <div class="footer">© 2017 VORENTIX · The documentary quality of your projects</div><div class="page">32</div>
</section>

<!-- Slide: four column circles -->
<section class="slide c3 r1">
  <h2 class="title"><span class="u">Four</span> Column Area</h2>
  <div class="brand"><span class="dot"></span>VORENTIX</div>
  <p class="lead" style="top:44px">Lorem ipsum dolor sit amet, consectetur adipiscing elit, sed do eiusmod tempor incididunt ut labore et dolore magna aliqua. Ut enimad minim veniam, quis nostrud exercitation ullamco laboris nisi ut aliquip ex ea commodo consequat.</p>
  <div class="vline" style="left:112px"></div><div class="vline" style="left:190px"></div><div class="vline" style="left:268px"></div>
  <div class="col" style="left:36px"><div class="circ dk"><i></i></div><h4>COLUMN 1</h4><p class="small">Lorem ipsum dolor sit amet, consectetur adipiscing elit, sed do eiusmod tempor incididunt ut labore et dolore magna aliqua.</p></div>
  <div class="col" style="left:115px"><div class="circ"><i></i></div><h4 class="lt">COLUMN 2</h4><p class="small">Lorem ipsum dolor sit amet, consectetur adipiscing elit, sed do eiusmod tempor incididunt ut labore et dolore magna aliqua.</p></div>
  <div class="col" style="left:193px"><div class="circ dk"><i></i></div><h4>COLUMN 3</h4><p class="small">Lorem ipsum dolor sit amet, consectetur adipiscing elit, sed do eiusmod tempor incididunt ut labore et dolore magna aliqua.</p></div>
  <div class="col" style="left:271px"><div class="circ"><i></i></div><h4 class="lt">COLUMN 4</h4><p class="small">Lorem ipsum dolor sit amet, consectetur adipiscing elit, sed do eiusmod tempor incididunt ut labore et dolore magna aliqua.</p></div>
  <div class="footer">© 2017 VORENTIX · The documentary quality of your projects</div><div class="page">33</div>
</section>

<!-- Slide: timeline -->
<section class="slide c1 r2">
  <h2 class="title"><span class="u">Timeline</span></h2>
  <div class="brand"><span class="dot"></span>VORENTIX</div>
  <svg class="abs" style="left:0;top:0" width="387" height="218">
    <line x1="50" y1="98" x2="335" y2="98" stroke="#cfcfcf" stroke-width="1"/>
    <g stroke="#cfcfcf" stroke-width="1">
      <line x1="98" y1="78" x2="98" y2="98"/><line x1="192" y1="78" x2="192" y2="98"/><line x1="290" y1="78" x2="290" y2="98"/>
      <line x1="144" y1="98" x2="144" y2="108"/><line x1="240" y1="98" x2="240" y2="108"/>
    </g>
    <path d="M340 115 Q338 127 328 129" fill="none" stroke="var(--blue)" stroke-width="0.7"/>
  </svg>
  <div class="tl" style="left:80px;top:38px;width:38px;height:38px;background:var(--blue-light)">2012<small>Your Text Goes Here</small></div>
  <div class="tl" style="left:172px;top:38px;width:38px;height:38px;background:var(--gray-dark)">2014<small>Your Text Goes Here</small></div>
  <div class="tl" style="left:270px;top:38px;width:38px;height:38px;background:var(--blue-light)">2016<small>Your Text Goes Here</small></div>
  <div class="tl" style="left:30px;top:78px;width:38px;height:38px;background:var(--blue)">2011<small>Your Text Goes Here</small></div>
  <div class="tl" style="left:124px;top:108px;width:38px;height:38px;background:var(--gray-light)">2013<small>Your Text Goes Here</small></div>
  <div class="tl" style="left:220px;top:108px;width:38px;height:38px;background:var(--gray-light)">2015<small>Your Text Goes Here</small></div>
  <div class="tl" style="left:316px;top:78px;width:38px;height:38px;background:var(--blue)">2017<small>Your Text Goes Here</small></div>
  <div class="abs" style="left:276px;top:132px;width:94px"><div class="head-s" style="color:var(--blue)">Your Text Goes Here</div><p class="small" style="font-size:4px">Lorem ipsum dolor sit amet, consectetur adipiscing elit, sed do eiusmod tempor incididunt ut labore et dolore magna aliqua</p></div>
  <div class="abs" style="left:17px;top:168px;width:180px"><div class="head-s" style="color:var(--blue)">Your Text Goes Here</div><p class="small" style="font-size:4px">Lorem ipsum dolor sit amet, consectetur adipiscing elit, sed do eiusmod tempor incididunt ut labore et dolore magna aliqua</p></div>
  <div class="footer">© 2017 VORENTIX · The documentary quality of your projects</div><div class="page">34</div>
</section>

<!-- Slide: workflow -->
<section class="slide c2 r2">
  <h2 class="title"><span class="u">Workflow</span> Area</h2>
  <div class="brand"><span class="dot"></span>VORENTIX</div>
  <p class="lead" style="top:54px">Lorem ipsum dolor sit amet, consectetur adipiscing elit, sed do eiusmod tempor incididunt ut labore et dolore magna aliqua. Ut enimad minim veniam, quis nostrud exercitation ullamco laboris nisi ut aliquip ex ea commodo consequat.</p>
  <svg class="abs" style="left:0;top:92px" width="387" height="90">
    <g fill="none" stroke-width="12">
      <path d="M28 42 A33 33 0 0 1 94 42" stroke="var(--blue)"/>
      <path d="M94 42 A34 34 0 0 0 162 42" stroke="var(--blue-light)"/>
      <path d="M162 42 A33 33 0 0 1 228 42" stroke="var(--blue)"/>
      <path d="M228 42 A34 34 0 0 0 296 42" stroke="var(--blue-light)"/>
      <path d="M296 42 A33 33 0 0 1 362 42" stroke="var(--blue)"/>
    </g>
    <g fill="#fff" stroke-width="1">
      <circle cx="38" cy="24" r="5" stroke="var(--blue)"/><circle cx="106" cy="62" r="5" stroke="var(--blue-light)"/>
      <circle cx="172" cy="24" r="5" stroke="var(--blue)"/><circle cx="240" cy="62" r="5" stroke="var(--blue-light)"/>
      <circle cx="306" cy="24" r="5" stroke="var(--blue)"/>
    </g>
    <g font-size="5" text-anchor="middle" font-family="Raleway, sans-serif">
      <text x="38" y="26" fill="var(--blue)">1</text><text x="106" y="64" fill="var(--blue-light)">2</text>
      <text x="172" y="26" fill="var(--blue)">3</text><text x="240" y="64" fill="var(--blue-light)">4</text>
      <text x="306" y="26" fill="var(--blue)">5</text>
    </g>
  </svg>
  <div class="abs" style="left:37px;top:142px;width:44px;text-align:center"><div class="head-s" style="font-weight:700;color:var(--blue)">Data 1</div><p class="small" style="font-size:4px">Lorem ipsum dolor sit amet, consectetur adipiscing elit.</p></div>
  <div class="abs" style="left:104px;top:80px;width:44px;text-align:center"><div class="head-s" style="font-weight:700;color:var(--blue)">Data 2</div><p class="small" style="font-size:4px">Lorem ipsum dolor sit amet, consectetur adipiscing elit.</p></div>
  <div class="abs" style="left:172px;top:142px;width:44px;text-align:center"><div class="head-s" style="font-weight:700;color:var(--blue)">Data 3</div><p class="small" style="font-size:4px">Lorem ipsum dolor sit amet, consectetur adipiscing elit.</p></div>
  <div class="abs" style="left:238px;top:80px;width:44px;text-align:center"><div class="head-s" style="font-weight:700;color:var(--blue)">Data 4</div><p class="small" style="font-size:4px">Lorem ipsum dolor sit amet, consectetur adipiscing elit.</p></div>
  <div class="abs" style="left:306px;top:142px;width:44px;text-align:center"><div class="head-s" style="font-weight:700;color:var(--blue)">Data 5</div><p class="small" style="font-size:4px">Lorem ipsum dolor sit amet, consectetur adipiscing elit.</p></div>
  <div class="footer">© 2017 VORENTIX · The documentary quality of your projects</div><div class="page">35</div>
</section>

<!-- Slide: bullet & bar chart -->
<section class="slide c3 r2">
  <h2 class="title"><span class="u">Bullet</span> &amp; Chart Area</h2>
  <div class="brand"><span class="dot"></span>VORENTIX</div>
  <svg class="abs" style="left:20px;top:58px" width="170" height="112" font-family="Raleway, sans-serif" font-size="3.6" fill="#777">
    <line x1="38" y1="0" x2="38" y2="100" stroke="#ddd" stroke-width="0.5"/>
    <text x="0" y="13">Category 4</text>
    <rect x="38" y="4" width="107" height="4" fill="var(--gray)"/><rect x="38" y="9" width="60" height="4" fill="var(--gray-light)"/><rect x="38" y="14" width="98" height="4" fill="var(--blue)"/>
    <text x="0" y="40">Category 3</text>
    <rect x="38" y="30" width="66" height="4" fill="var(--gray)"/><rect x="38" y="35" width="60" height="4" fill="var(--gray-light)"/><rect x="38" y="40" width="70" height="4" fill="var(--blue)"/>
    <text x="0" y="66">Category 2</text>
    <rect x="38" y="56" width="40" height="4" fill="var(--gray)"/><rect x="38" y="61" width="97" height="4" fill="var(--gray-light)"/><rect x="38" y="66" width="57" height="4" fill="var(--blue)"/>
    <text x="0" y="92">Category 1</text>
    <rect x="38" y="82" width="66" height="4" fill="var(--gray)"/><rect x="38" y="87" width="48" height="4" fill="var(--gray-light)"/><rect x="38" y="92" width="95" height="4" fill="var(--blue)"/>
    <g font-size="3.2"><rect x="58" y="106" width="3" height="3" fill="var(--gray)"/><text x="63" y="109">Series 1</text><rect x="80" y="106" width="3" height="3" fill="var(--gray-light)"/><text x="85" y="109">Series 2</text><rect x="102" y="106" width="3" height="3" fill="var(--blue)"/><text x="107" y="109">Series 3</text></g>
  </svg>
  <div class="bul" style="left:196px;top:60px"><span class="ico"></span><div><h5>Category One</h5><p class="small" style="font-size:4px">Lorem ipsum dolor sit amet, consectetur adipiscing elit, sed do eiusmod</p></div></div>
  <div class="bul" style="left:196px;top:90px"><span class="ico lt"></span><div><h5 class="lt">Category Two</h5><p class="small" style="font-size:4px">Lorem ipsum dolor sit amet, consectetur adipiscing elit, sed do eiusmod</p></div></div>
  <div class="bul" style="left:196px;top:120px"><span class="ico"></span><div><h5>Category Three</h5><p class="small" style="font-size:4px">Lorem ipsum dolor sit amet, consectetur adipiscing elit, sed do eiusmod</p></div></div>
  <div class="bul" style="left:196px;top:150px"><span class="ico lt"></span><div><h5 class="lt">Category Four</h5><p class="small" style="font-size:4px">Lorem ipsum dolor sit amet, consectetur adipiscing elit, sed do eiusmod</p></div></div>
  <div class="footer">© 2017 VORENTIX · The documentary quality of your projects</div><div class="page">36</div>
</section>

<!-- Slide: table -->
<section class="slide c1 r3">
  <h2 class="title" style="left:140px;top:12px;color:var(--blue-mid)">Table Area</h2>
  <div class="brand"><span class="dot"></span>VORENTIX</div>
  <table class="grid">
    <colgroup><col style="width:120px"><col style="width:136px"><col style="width:38px"><col style="width:38px"><col style="width:44px"></colgroup>
    <thead><tr><th>Description</th><th>Column 1</th><th>Silver<small>$50K</small></th><th>Gold<small>$75K</small></th><th>Platinum<small>$125K</small></th></tr></thead>
    <tbody>
      <tr><td>Lorem ipsum dolor sit amet</td><td></td><td><i class="chk o">×</i></td><td><i class="chk o">×</i></td><td><i class="chk">✓</i></td></tr>
      <tr><td>Lorem ipsum dolor sit amet</td><td></td><td><i class="chk o">×</i></td><td><i class="chk o">×</i></td><td><i class="chk">✓</i></td></tr>
      <tr><td>Lorem ipsum dolor sit amet</td><td></td><td><i class="chk o">×</i></td><td><i class="chk">✓</i></td><td><i class="chk">✓</i></td></tr>
      <tr><td>Lorem ipsum dolor sit amet</td><td></td><td><i class="chk o">×</i></td><td><i class="chk">✓</i></td><td><i class="chk">✓</i></td></tr>
      <tr><td>Lorem ipsum dolor sit amet</td><td></td><td><i class="chk o">×</i></td><td><i class="chk">✓</i></td><td><i class="chk">✓</i></td></tr>
      <tr><td>Lorem ipsum dolor sit amet</td><td></td><td><i class="chk o">×</i></td><td><i class="chk">✓</i></td><td><i class="chk">✓</i></td></tr>
      <tr><td>Lorem ipsum dolor sit amet</td><td></td><td><i class="chk">✓</i></td><td><i class="chk">✓</i></td><td><i class="chk">✓</i></td></tr>
      <tr><td>Lorem ipsum dolor sit amet</td><td></td><td><i class="chk">✓</i></td><td><i class="chk">✓</i></td><td><i class="chk">✓</i></td></tr>
      <tr><td>Lorem ipsum dolor sit amet</td><td></td><td><i class="chk">✓</i></td><td><i class="chk">✓</i></td><td><i class="chk">✓</i></td></tr>
      <tr><td>Lorem ipsum dolor sit amet</td><td></td><td><i class="chk">✓</i></td><td><i class="chk">✓</i></td><td><i class="chk">✓</i></td></tr>
      <tr><td>Lorem ipsum dolor sit amet</td><td></td><td><i class="chk">✓</i></td><td><i class="chk">✓</i></td><td><i class="chk">✓</i></td></tr>
      <tr><td>Lorem ipsum dolor sit amet</td><td></td><td><i class="chk">✓</i></td><td><i class="chk">✓</i></td><td><i class="chk">✓</i></td></tr>
      <tr><td>Lorem ipsum dolor sit amet</td><td></td><td><i class="chk">✓</i></td><td><i class="chk">✓</i></td><td><i class="chk">✓</i></td></tr>
      <tr><td>Lorem ipsum dolor sit amet</td><td></td><td><i class="chk">✓</i></td><td><i class="chk">✓</i></td><td><i class="chk">✓</i></td></tr>
      <tr><td>Lorem ipsum dolor sit amet</td><td></td><td><i class="chk">✓</i></td><td><i class="chk">✓</i></td><td><i class="chk">✓</i></td></tr>
      <tr><td>Lorem ipsum dolor sit amet</td><td></td><td><i class="chk">✓</i></td><td><i class="chk">✓</i></td><td><i class="chk">✓</i></td></tr>
    </tbody>
  </table>
  <div class="footer">© 2017 VORENTIX · The documentary quality of your projects</div><div class="page">37</div>
</section>

<!-- Slide: bullet & donut chart -->
<section class="slide c2 r3">
  <h2 class="title"><span class="u">Bullet</span> &amp; Chart Area</h2>
  <div class="brand"><span class="dot"></span>VORENTIX</div>
  <div class="bul" style="left:36px;top:58px"><span class="ico"></span><div><h5>Your Text Here</h5><p class="small" style="font-size:4px">Lorem ipsum dolor sit amet, consectetur adipiscing elit, sed do eiusmod</p></div></div>
  <div class="bul" style="left:36px;top:88px"><span class="ico lt"></span><div><h5 class="lt">Your Text Here</h5><p class="small" style="font-size:4px">Lorem ipsum dolor sit amet, consectetur adipiscing elit, sed do eiusmod</p></div></div>
  <div class="bul" style="left:36px;top:118px"><span class="ico gd"></span><div><h5>Your Text Here</h5><p class="small" style="font-size:4px">Lorem ipsum dolor sit amet, consectetur adipiscing elit, sed do eiusmod</p></div></div>
  <div class="bul" style="left:36px;top:148px"><span class="ico gl"></span><div><h5 class="lt">Your Text Here</h5><p class="small" style="font-size:4px">Lorem ipsum dolor sit amet, consectetur adipiscing elit, sed do eiusmod</p></div></div>
  <svg class="abs" style="left:180px;top:48px" width="200" height="152" font-family="Raleway, sans-serif">
    <g transform="translate(96 76) rotate(-90)" fill="none" stroke-width="16">
      <circle r="34" stroke="var(--blue)" stroke-dasharray="128.2 213.6"/>
      <circle r="34" stroke="var(--blue-light)" stroke-dasharray="53.4 213.6" stroke-dashoffset="-128.2"/>
      <circle r="34" stroke="var(--gray-dark)" stroke-dasharray="32 213.6" stroke-dashoffset="-181.6"/>
      <circle r="34" stroke="var(--gray-light)" stroke-dasharray="21.4 213.6" stroke-dashoffset="-213.6"/>
    </g>
    <g fill="var(--blue)"><rect x="86" y="73" width="3" height="8"/><rect x="91" y="69" width="3" height="12"/><rect x="96" y="65" width="3" height="16"/><rect x="101" y="61" width="3" height="20"/><rect x="84" y="82" width="22" height="1"/></g>
    <g font-size="10" fill="var(--blue)"><text x="146" y="81">60%</text><text x="16" y="128">25%</text><text x="20" y="56" fill="var(--gray)">15%</text><text x="58" y="22" fill="var(--gray)">10%</text></g>
    <g font-size="3.4" fill="#777"><rect x="58" y="143" width="3" height="3" fill="var(--blue)"/><text x="63" y="146">1st Qtr</text><rect x="78" y="143" width="3" height="3" fill="var(--blue-light)"/><text x="83" y="146">2nd Qtr</text><rect x="99" y="143" width="3" height="3" fill="var(--gray-dark)"/><text x="104" y="146">3rd Qtr</text><rect x="119" y="143" width="3" height="3" fill="var(--gray-light)"/><text x="124" y="146">4th Qtr</text></g>
  </svg>
  <div class="footer">© 2017 VORENTIX · The documentary quality of your projects</div><div class="page">38</div>
</section>

<!-- Slide: infographic area -->
<section class="slide c3 r3">
  <h2 class="title"><span class="u">Infographic</span> Area</h2>
  <div class="abs" style="left:52px;top:46px;width:46px;height:44px;border-radius:6px;background:linear-gradient(var(--blue-pale),var(--blue-mid))" role="img" aria-label="Stacked layers graphic with four levels"></div>
  <svg class="abs" style="left:98px;top:46px" width="30" height="44" font-family="Raleway, sans-serif">
    <g stroke="#999" stroke-width="0.4"><line x1="0" y1="8" x2="14" y2="8"/><line x1="0" y1="17" x2="14" y2="17"/><line x1="0" y1="26" x2="14" y2="26"/><line x1="0" y1="35" x2="14" y2="35"/></g>
    <g font-size="4.5" fill="#555"><text x="15" y="10">01</text><text x="15" y="19">02</text><text x="15" y="28">03</text><text x="15" y="37">04</text></g>
  </svg>
  <div class="abs" style="left:62px;top:116px;width:40px;height:40px;border-radius:4px;background:linear-gradient(var(--blue),var(--blue-light))" role="img" aria-label="Twisted ribbon with four option labels"></div>
  <svg class="abs" style="left:140px;top:64px" width="80" height="112" font-family="Raleway, sans-serif">
    <g font-size="5" fill="#555"><text x="6" y="8">95%</text><text x="30" y="8">60%</text><text x="55" y="8">65%</text></g>
    <rect x="6" y="16" width="18" height="76" fill="var(--blue-mid)"/><rect x="30" y="40" width="18" height="52" fill="var(--blue-mid)"/><rect x="54" y="36" width="18" height="56" fill="var(--gray-light)"/>
    <line x1="0" y1="96" x2="78" y2="96" stroke="var(--blue)" stroke-width="1"/>
    <g fill="var(--blue)"><rect x="11" y="101" width="8" height="4"/><rect x="35" y="101" width="8" height="4"/><rect x="59" y="101" width="8" height="4"/></g>
  </svg>
  <div class="abs" style="left:256px;top:42px;width:36px;height:9px;background:var(--blue);color:#fff;font-size:6px;line-height:9px;padding-left:3px">65% YES</div>
  <div class="abs" style="left:256px;top:53px;width:36px;height:27px;background:linear-gradient(var(--blue) 65%,var(--blue-pale) 65%)" role="img" aria-label="Grid of people figures showing a yes and no split"></div>
  <div class="abs" style="left:256px;top:82px;width:36px;height:9px;background:var(--blue-light);color:#fff;font-size:6px;line-height:9px;padding-left:3px">NO 35%</div>
  <svg class="abs" style="left:240px;top:108px" width="90" height="66" font-family="Raleway, sans-serif">
    <g font-size="4" fill="#fff">
      <polygon points="0,2 70,2 76,8 70,14 0,14" fill="var(--blue)"/><text x="14" y="9.5">01 OPTION</text>
      <polygon points="6,17 76,17 70,23 76,29 6,29" fill="var(--blue-light)"/><text x="22" y="24.5">02 OPTION</text>
      <polygon points="0,32 70,32 76,38 70,44 0,44" fill="var(--blue)"/><text x="14" y="39.5">03 OPTION</text>
      <polygon points="6,47 76,47 70,53 76,59 6,59" fill="var(--blue-light)"/><text x="22" y="54.5">04 OPTION</text>
    </g>
  </svg>
</section>

<!-- Slide: our infographic -->
<section class="slide c1 r4">
  <h2 class="title"><span class="u">Our</span> Infographic</h2>
  <div class="brand"><span class="dot"></span>VORENTIX</div>
  <div class="strip dk" style="top:62px">Lorem ipsum dolor sit amet, consectetur adipiscing elit, sed do eiusmod tempor incididunt ut labore et dolore magna aliqua. Ut enim ad minim veniam.</div>
  <div class="strip lt" style="top:81px">Lorem ipsum dolor sit amet, consectetur adipiscing elit, sed do eiusmod tempor incididunt ut labore et dolore magna aliqua. Ut enim ad minim veniam.</div>
  <div class="strip dk" style="top:100px">Lorem ipsum dolor sit amet, consectetur adipiscing elit, sed do eiusmod tempor incididunt ut labore et dolore magna aliqua. Ut enim ad minim veniam.</div>
  <div class="strip lt" style="top:119px">Lorem ipsum dolor sit amet, consectetur adipiscing elit, sed do eiusmod tempor incididunt ut labore et dolore magna aliqua. Ut enim ad minim veniam.</div>
  <div class="abs" style="left:54px;top:46px;width:106px;height:106px;border-radius:50%;background:#cfcfcf;display:flex;align-items:center;justify-content:center">
    <div style="width:88px;height:88px;border-radius:50%;background:var(--blue);color:#fff;text-align:center;font-weight:700;font-size:11px;display:flex;flex-direction:column;align-items:center;justify-content:center;gap:4px"><span style="width:12px;height:12px;border-radius:50%;background:#fff"></span>VORENTIX</div>
  </div>
  <p class="lead" style="top:178px;text-align:center;font-size:4.6px">Lorem ipsum dolor sit amet, consectetur adipiscing elit, sed do eiusmod tempor incididunt ut labore et dolore magna aliqua. Ut enim ad minim veniam, quis nostrud exercitation ullamco laboris nisi ut aliquip ex ea commodo consequat.</p>
  <div class="footer">© 2017 VORENTIX · The documentary quality of your projects</div><div class="page">40</div>
</section>

<!-- Slide: team -->
<section class="slide c2 r4">
  <div class="photo" style="left:0;top:0;width:120px;height:210px;background:linear-gradient(160deg,#e3eef4,#a9c3d3 55%,#6c8ea6)" role="img" aria-label="Team of engineers in hard hats reviewing building plans"></div>
  <div class="abs" style="left:0;top:146px;width:120px;height:40px;background:rgba(52,167,215,.55)"></div>
  <div class="abs" style="left:8px;top:152px;font-size:13px;color:#fff">Meet Our Team</div>
  <div class="brand"><span class="dot"></span>VORENTIX</div>
  <div class="abs" style="left:128px;top:10px;width:48px;height:48px;border-radius:50%;border:2px solid #fff;box-shadow:0 0 0 1px #ddd;background:linear-gradient(#d2c3b4,#6e6762)" role="img" aria-label="Portrait of the president and CEO"></div>
  <div class="abs" style="left:184px;top:20px;line-height:1.3"><b style="font-size:7px;font-weight:500;color:#555">Lucas Ferrand</b><br><span style="font-size:5px;color:var(--blue)">President &amp; CEO</span><br><em style="font-style:normal;font-size:3.8px;color:#999">lucas@vorentix.fr</em></div>
  <div class="person" style="left:160px;top:72px"><div class="face" role="img" aria-label="Portrait of the VP of marketing"></div><b>Hugo Marchal</b><span>VP Marketing</span><em>hugo@vorentix.fr</em></div>
  <div class="person" style="left:260px;top:72px"><div class="face" role="img" aria-label="Portrait of the VP of finance"></div><b>Noah Berthier</b><span>VP Finance</span><em>noah@vorentix.fr</em></div>
  <div class="person" style="left:160px;top:136px"><div class="face" role="img" aria-label="Portrait of the VP of business development"></div><b>Theo Rivaud</b><span>VP of Business Development</span><em>theo@vorentix.fr</em></div>
  <div class="person" style="left:260px;top:136px"><div class="face" role="img" aria-label="Portrait of the marketing manager"></div><b>Clara Dumont</b><span>Manager Marketing</span><em>clara@vorentix.fr</em></div>
  <div class="footer">© 2017 VORENTIX · The documentary quality of your projects</div><div class="page">41</div>
</section>

<!-- Slide: contact -->
<section class="slide c3 r4">
  <div class="photo contact-bg" role="img" aria-label="Hand writing on paper at a desk, tinted blue"></div>
  <div class="contact-panel"></div>
  <div class="contact-brand"><span class="dot"></span>VORENTIX</div>
  <h2 class="contact-title"><span>Our</span> Contact</h2>
  <div class="cline" style="top:106px"><svg width="7" height="7" viewBox="0 0 10 10"><path d="M1 5 L5 1 L9 5 V9 H1Z" fill="#fff"/></svg><span>18 Rue Calvel<br>Paris 75011</span></div>
  <div class="cline" style="top:128px"><svg width="7" height="7" viewBox="0 0 10 10"><path d="M2 1 L4 1 L5 3 L4 4 Q5 6 6 6 L7 5 L9 6 L9 8 Q8 9 7 9 Q1 8 1 2 Q1 1 2 1Z" fill="#fff"/></svg><span>(01) 482-6630</span></div>
  <div class="cline" style="top:144px"><svg width="7" height="7" viewBox="0 0 10 10"><rect x="1" y="2" width="8" height="6" fill="#fff"/></svg><span>contact@vorentix.fr</span></div>
  <div class="cline" style="top:160px"><svg width="7" height="7" viewBox="0 0 10 10"><circle cx="5" cy="5" r="4" fill="#fff"/></svg><span>www.vorentix.fr</span></div>
  <div class="social"><i></i><i></i><i></i></div>
  <div class="thanks"><h2>THANK YOU</h2><h3>For Your Precious Time</h3><p>Stop by our office or give us a call!<br>We would love to hear from you.</p></div>
</section>

</body>
</html>
```